Harborlane Products Flyer

Harborlane Lending Group, Inc.
Licensed Mortgage Company
Serving the DMV since 1997
"You open the Harborlane, we'll carry the load"
We specialize in...
FHA Loans
* Credit Scores as low as 500
* 203K Renovation Loans
Conventional Loans
* As little as 1% Down
* Bank Statement for Self-Employed
Investor Loans
* DSCR, & Fix & Flip
* Commercial & New Construction
Other Programs
* HELOCS & Reverse Mortgages
Call today for a free consultation
(800) 914-6027
www.harborlanehomeloans.com
NMLS #731860

```html
<!DOCTYPE html>
<html lang="en">
<head>
<meta charset="utf-8">
<title>Harborlane Products Flyer</title>
<link href="https://fonts.googleapis.com/css2?family=Cinzel:wght@600;700;800&family=Nunito:wght@500;700;800&display=swap" rel="stylesheet">
<style>
  :root {
    --blue: #0b5a8a;
    --blue-deep: #084b74;
    --gold: #b9a532;
    --gold-light: #d6c548;
    --green: #8cc63f;
    --sky: #e0f1fb;
    --ink: #1f2a33;
    --white: #ffffff;
    --stage: #e8e5e0;
  }
  * { margin: 0; padding: 0; box-sizing: border-box; }
  html, body { width: 1200px; height: 1117px; overflow: hidden; background: var(--stage); }
  .flyer {
    position: absolute; left: 219px; top: 20px;
    width: 762px; height: 1077px;
    background: var(--white); overflow: hidden;
    box-shadow: 0 6px 24px rgba(0,0,0,.18);
    font-family: "Nunito", sans-serif;
  }
  .flyer-art { position: absolute; inset: 0; width: 762px; height: 1077px; }
  .brand-mark {
    position: absolute; left: 40px; top: 96px; width: 270px; text-align: center;
  }
  .brand-mark__name {
    display: inline-flex; align-items: center; gap: 8px;
    font-family: "Cinzel", serif; font-weight: 700; font-size: 30px; color: var(--blue);
  }
  .brand-mark__dot { width: 14px; height: 14px; border-radius: 50%; background: var(--gold); }
  .brand-mark__tagline {
    margin-top: 8px; font-size: 9.5px; font-weight: 800; color: var(--blue);
    text-transform: uppercase; letter-spacing: .2px;
  }
  .brand-mark__est {
    margin-top: 4px; font-family: "Cinzel", serif; font-weight: 700; font-size: 11px;
    color: var(--ink); letter-spacing: 1.5px;
  }
  .headline { position: absolute; left: 54px; top: 262px; font-family: "Cinzel", serif; }
  .headline__name { font-weight: 800; font-size: 40px; color: var(--blue); line-height: 1; letter-spacing: -.5px; }
  .headline__sub {
    margin-top: 48px; font-weight: 700; font-size: 33px; line-height: 1.1; color: var(--gold);
  }
  .band-title {
    position: absolute; left: 320px; top: 516px; width: 442px; text-align: center;
    font-family: "Cinzel", serif; font-weight: 700; font-size: 29px; line-height: 1.02; color: var(--white);
  }
  .since {
    position: absolute; left: 400px; top: 620px; width: 340px; text-align: center;
    font-family: "Cinzel", serif; font-weight: 700; font-size: 30px; line-height: 1.1; color: var(--blue);
  }
  .since__year { color: var(--green); font-size: 42px; }
  .specialize {
    position: absolute; left: 58px; top: 719px;
    font-family: "Cinzel", serif; font-weight: 700; font-size: 25px; color: var(--white);
  }
  .products { position: absolute; top: 775px; display: flex; flex-direction: column; gap: 14px; }
  .products--left { left: 56px; }
  .products--right { left: 397px; }
  .product__title { font-weight: 800; font-size: 18px; color: var(--blue); line-height: 1.3; }
  .product__list { list-style: none; }
  .product__item {
    display: flex; align-items: center; gap: 9px;
    font-weight: 500; font-size: 16.5px; color: var(--ink); line-height: 1.35;
  }
  .product__tick { width: 13px; height: 13px; flex: none; }
  .cta {
    position: absolute; left: 56px; top: 988px;
    font-family: "Cinzel", serif; font-weight: 700; font-size: 25px; line-height: 1.28; color: var(--white);
  }
  .cta__accent { color: var(--green); }
  .contact { position: absolute; left: 442px; top: 965px; font-family: "Cinzel", serif; font-weight: 700; }
  .contact__row { display: flex; align-items: center; gap: 8px; color: var(--blue); }
  .contact__phone { font-size: 30px; }
  .contact__web { font-size: 14px; margin-top: 2px; }
  .contact__icon { width: 18px; height: 18px; flex: none; }
  .contact__license {
    display: flex; align-items: center; gap: 10px; margin-top: 8px; margin-left: -10px;
    font-size: 17px; color: var(--gold);
  }
  .contact__rule { width: 118px; height: 1px; background: var(--gold); }
</style>
</head>
<body>
<main class="flyer">
  <svg class="flyer-art" viewBox="0 0 762 1077" xmlns="http://www.w3.org/2000/svg">
    <defs>
      <linearGradient id="hero-tones" x1="0" y1="0" x2="0" y2="1">
        <stop offset="0" stop-color="#b7b0a2"/>
        <stop offset=".55" stop-color="#6f7a5a"/>
        <stop offset="1" stop-color="#4f8a2f"/>
      </linearGradient>
      <linearGradient id="family-tones" x1="0" y1="0" x2="1" y2="1">
        <stop offset="0" stop-color="#d9d3c9"/>
        <stop offset=".5" stop-color="#8c6e55"/>
        <stop offset="1" stop-color="#4b5c78"/>
      </linearGradient>
      <linearGradient id="pill-tones" x1="0" y1="0" x2="1" y2="0">
        <stop offset="0" stop-color="#b9a532"/>
        <stop offset=".6" stop-color="#d2c03f"/>
        <stop offset="1" stop-color="#b9a532"/>
      </linearGradient>
    </defs>

    <!-- hero ring and photo -->
    <circle cx="605" cy="241" r="279" fill="none" stroke="var(--green)" stroke-width="5"/>
    <circle cx="605" cy="241" r="266" fill="var(--blue)"/>
    <circle cx="605" cy="241" r="248" fill="#fff"/>
    <circle cx="605" cy="241" r="244" fill="url(#hero-tones)" role="img" aria-label="Family celebrating in front of their new house holding a home for sale sign"/>

    <!-- title band -->
    <path d="M150 495 H762 V597 H300 Z" fill="var(--blue)"/>

    <!-- family photo -->
    <path d="M0 598 Q150 480 270 515 Q360 545 392 708 H0 Z" fill="url(#family-tones)" stroke="#fff" stroke-width="5" role="img" aria-label="Smiling family relaxing together on a sofa at home"/>

    <!-- light backdrop -->
    <rect x="723" y="842" width="39" height="110" fill="var(--sky)"/>
    <rect x="0" y="952" width="762" height="125" fill="var(--sky)"/>

    <!-- specialize pill and frame -->
    <path d="M0 714 H423 A20 20 0 0 1 423 754 H0 Z" fill="url(#pill-tones)"/>
    <path d="M449 732 H723 V950 H0" fill="none" stroke="var(--green)" stroke-width="2"/>

    <!-- call to action block -->
    <path d="M0 967 H372 Q385 967 390 978 L421 1077 H0 Z" fill="var(--blue)"/>
  </svg>

  <div class="brand-mark">
    <div class="brand-mark__name"><span class="brand-mark__dot"></span>Harborlane</div>
    <div class="brand-mark__tagline">You open the Harborlane, we'll carry the load</div>
    <div class="brand-mark__est">EST. 1997</div>
  </div>

  <h1 class="headline">
    <div class="headline__name">Harborlane</div>
    <div class="headline__sub">Lending Group,<br>Inc.</div>
  </h1>

  <h2 class="band-title">Licensed Mortgage<br>Company</h2>

  <p class="since">Serving the DMV<br>since <span class="since__year">1997</span></p>

  <h3 class="specialize">We specialize in...</h3>

  <div class="products products--left">
    <section class="product">
      <h4 class="product__title">FHA Loans</h4>
      <ul class="product__list">
        <li class="product__item"><svg class="product__tick" viewBox="0 0 12 12"><path d="M1 6.5 4.5 10 11 2" fill="none" stroke="var(--green)" stroke-width="2.2"/></svg>Credit Scores as low as 500</li>
        <li class="product__item"><svg class="product__tick" viewBox="0 0 12 12"><path d="M1 6.5 4.5 10 11 2" fill="none" stroke="var(--green)" stroke-width="2.2"/></svg>203K Renovation Loans</li>
      </ul>
    </section>
    <section class="product">
      <h4 class="product__title">Conventional Loans</h4>
      <ul class="product__list">
        <li class="product__item"><svg class="product__tick" viewBox="0 0 12 12"><path d="M1 6.5 4.5 10 11 2" fill="none" stroke="var(--green)" stroke-width="2.2"/></svg>As little as 1% Down</li>
        <li class="product__item"><svg class="product__tick" viewBox="0 0 12 12"><path d="M1 6.5 4.5 10 11 2" fill="none" stroke="var(--green)" stroke-width="2.2"/></svg>Bank Statement for Self-Employed</li>
      </ul>
    </section>
  </div>

  <div class="products products--right">
    <section class="product">
      <h4 class="product__title">Investor Loans</h4>
      <ul class="product__list">
        <li class="product__item"><svg class="product__tick" viewBox="0 0 12 12"><path d="M1 6.5 4.5 10 11 2" fill="none" stroke="var(--green)" stroke-width="2.2"/></svg>DSCR, &amp; Fix &amp; Flip</li>
        <li class="product__item"><svg class="product__tick" viewBox="0 0 12 12"><path d="M1 6.5 4.5 10 11 2" fill="none" stroke="var(--green)" stroke-width="2.2"/></svg>Commercial &amp; New Construction</li>
      </ul>
    </section>
    <section class="product">
      <h4 class="product__title">Other Programs</h4>
      <ul class="product__list">
        <li class="product__item"><svg class="product__tick" viewBox="0 0 12 12"><path d="M1 6.5 4.5 10 11 2" fill="none" stroke="var(--green)" stroke-width="2.2"/></svg>HELOCS &amp; Reverse Mortgages</li>
      </ul>
    </section>
  </div>

  <p class="cta">Call today for a<br><span class="cta__accent">Free consultation</span></p>

  <div class="contact">
    <div class="contact__row contact__phone">
      <svg class="contact__icon" viewBox="0 0 24 24"><path d="M6.6 2.5c.6-.4 1.4-.2 1.8.4l2 3.2c.4.6.2 1.3-.3 1.7L8.6 8.9c.9 2.6 3 4.9 5.6 6l1.2-1.5c.4-.5 1.2-.7 1.7-.3l3.2 2c.6.4.8 1.2.4 1.8l-1.3 2.300c-.5.8-1.4 1.2-2.3 1C9.3 18.8 4.5 13.7 3.3 6.8c-.2-.9.2-1.8 1-2.3Z" fill="var(--gold)"/></svg>
      (800) 914-6027
    </div>
    <div class="contact__row contact__web">
      <svg class="contact__icon" viewBox="0 0 24 24"><circle cx="12" cy="12" r="10" fill="var(--gold)"/><path d="M2 12h20M12 2c3 3 3 17 0 20M12 2c-3 3-3 17 0 20" fill="none" stroke="#fff" stroke-width="1.4"/></svg>
      www.harborlanehomeloans.com
    </div>
    <div class="contact__license"><span class="contact__rule"></span>NMLS #731860</div>
  </div>
</main>
</body>
</html>
```